Quorbelline.io - Please redesign to make it look better from current design

We already have the current website, that you can access but we think it can improve from current version.
Quorbelline is a cryptocurrency hedge fund that allow you to participate in the hedge fund with cryptocurrency such as eth.
At current phase, we are doing an ICO, then we want to make sure that the website it looks professional, beautiful and trustable enough for investors after looking at our website.
Target Market(s)
Investors
Industry/Entity Type
Investment
Coding
Coded - Design and coding required
Number of Pages Required
1 page
Look and feel
Each slider illustrates characteristics of the customer's brand and the style your logo design should communicate.

```html
<!DOCTYPE html>
<html lang="en">
<head>
<meta charset="utf-8">
<title>Quorbelline.io – Digital Asset Management</title>
<link href="https://fonts.googleapis.com/css2?family=Jost:wght@400;500;600&family=Mulish:wght@400;600;700&display=swap" rel="stylesheet">
<style>
:root{
  --navy:#1b2a8c;
  --ink:#1d2b86;
  --sky:#c9eefa;
  --text:#4a5470;
  --white:#ffffff;
  --black:#000000;
  --step-1:#1a2790;
  --step-2:#1f33b4;
  --step-3:#2740d2;
  --step-4:#3552da;
  --step-5:#4b69e3;
}
*{box-sizing:border-box;margin:0;padding:0}
html,body{width:1200px;height:3214px;overflow:hidden}
body{font-family:"Mulish",sans-serif;color:var(--text);background:var(--white);position:relative}
.heading{font-family:"Jost",sans-serif;font-weight:500;color:var(--ink);text-transform:uppercase;text-align:center}

/* header */
.site-header{position:absolute;top:0;left:0;width:1200px;height:140px;background:var(--sky);display:flex;align-items:center;padding:0 76px}
.brand{display:flex;align-items:center;gap:12px;font-family:"Jost",sans-serif;font-weight:600;font-size:30px;color:var(--navy)}
.brand-dot{width:22px;height:22px;border-radius:50%;background:var(--navy)}
.main-nav{margin-left:auto;display:flex;align-items:center;gap:34px;font-family:"Jost",sans-serif;font-size:17px;color:var(--navy)}
.main-nav .active{color:#2d6bd6}
.btn-download{background:var(--navy);color:var(--white);border-radius:30px;padding:14px 30px;font-weight:500;font-size:19px;margin-left:6px}

/* hero */
.hero{position:absolute;top:140px;left:0;width:1200px;height:535px;background:var(--sky)}
.hero-card{position:absolute;left:375px;top:16px;width:461px;height:247px;background:var(--white);border:8px solid var(--navy);padding:22px 30px;text-align:center}
.hero-card h1{font-size:37px;line-height:44px}
.hero-card p{font-size:15px;font-style:italic;line-height:26px;margin-top:14px;color:#3a4260}
.hero-scene{position:absolute;left:0;top:267px;width:1200px;height:268px;background:linear-gradient(180deg,#bfe9f7 0%,#8fd0ea 55%,#2b64a8 100%)}

/* definition */
.definition{position:absolute;top:675px;left:0;width:1200px;height:386px;background:var(--navy);text-align:center;color:#c9d2f5}
.definition .mark{width:40px;height:40px;border-radius:50%;background:var(--white);margin:44px auto 0}
.definition h2{color:var(--white);font-size:40px;line-height:48px;margin-top:22px}
.definition p{width:1000px;margin:20px auto 0;font-size:14px;line-height:27px}
.btn-outline{display:inline-block;margin-top:20px;border:2px solid var(--white);border-radius:30px;padding:12px 28px;color:var(--white);font-family:"Jost",sans-serif;font-weight:500;font-size:18px;text-transform:uppercase}

/* process */
.process{position:absolute;top:1061px;left:0;width:1200px;height:643px;background:var(--white)}
.process h2{font-size:40px;line-height:52px;margin-top:50px}
.subtitle{text-align:center;font-size:19px;line-height:24px;color:#4a4f66;margin-top:4px}
.process p{width:900px;margin:12px auto 0;text-align:center;font-size:14px;line-height:28px}
.process-visual{position:absolute;left:182px;top:236px;width:836px;height:407px;background:linear-gradient(180deg,#eef3f6 0%,#d9eef5 60%,#c9a48f 100%);border-radius:24px 24px 0 0}
.side-wedge{position:absolute;top:1560px;width:80px;height:144px;background:var(--sky)}
.side-wedge.left{left:0;clip-path:polygon(0 0,100% 100%,0 100%)}
.side-wedge.right{right:0;clip-path:polygon(100% 0,100% 100%,0 100%)}

/* fee steps */
.fee-steps{position:absolute;top:1704px;left:80px;width:1040px;height:225px;display:flex}
.fee-step{flex:1;display:flex;flex-direction:column;color:var(--white);text-align:center}
.fee-step:nth-child(1){background:var(--step-1)}
.fee-step:nth-child(2){background:var(--step-2)}
.fee-step:nth-child(3){background:var(--step-3)}
.fee-step:nth-child(4){background:var(--step-4)}
.fee-step:nth-child(5){background:var(--step-5)}
.fee-cell{height:112px;display:flex;align-items:center;justify-content:center;padding:0 26px;font-size:14px;line-height:26px}
.fee-value{font-family:"Jost",sans-serif;font-size:38px;font-weight:500}
.reinvest{position:absolute;top:1929px;left:0;width:1200px;height:68px;background:var(--black);color:var(--white);text-align:center;font-size:23px;line-height:68px}

/* team */
.team{position:absolute;top:1997px;left:0;width:1200px;height:564px;background:var(--white)}
.team h2{font-size:38px;line-height:48px;margin-top:52px}
.team-card{position:absolute;top:153px;width:313px;height:343px;background:var(--sky);text-align:center;padding:0 24px}
.team-card.featured{background:var(--white);box-shadow:0 4px 14px rgba(0,0,0,.28);border-bottom:4px solid var(--navy)}
.team-card.featured::after{content:"";position:absolute;left:146px;bottom:-14px;border:10px solid transparent;border-top-color:var(--navy)}
.portrait{width:146px;height:146px;border-radius:50%;margin:20px auto 0;border:4px solid var(--white);background:radial-gradient(circle at 50% 40%,#c99a78 0%,#8a6048 55%,#3a3f52 100%)}
.team-card h3{font-family:"Jost",sans-serif;font-weight:500;font-size:18px;line-height:24px;color:var(--navy);margin-top:22px;text-transform:uppercase}
.role{font-size:15px;line-height:20px;color:#333;margin-top:4px}
.team-card p{font-size:13px;line-height:22px;margin-top:10px}

/* more info */
.more-info{position:absolute;top:2561px;left:0;width:1200px;height:364px;background:var(--sky)}
.more-info .slant{position:absolute;inset:0;background:var(--white);clip-path:polygon(0 0,100% 0,100% 22%,0 58%)}
.big-mark{position:absolute;left:90px;top:80px;height:100px;display:flex;align-items:center;gap:14px;font-family:"Jost",sans-serif;font-weight:600;font-size:48px;color:var(--navy)}
.big-mark .dot{width:42px;height:42px;border-radius:50%;background:var(--navy);flex:none}
.more-info h2{position:absolute;left:473px;top:150px;font-size:40px;line-height:46px;text-align:left}
.more-info p{position:absolute;left:473px;top:204px;width:660px;font-size:14px;line-height:26px}
.btn-solid{position:absolute;left:470px;top:264px;background:var(--navy);color:var(--white);border-radius:30px;padding:13px 30px;font-family:"Jost",sans-serif;font-weight:500;font-size:19px;line-height:24px;text-transform:uppercase}

/* footer */
.site-footer{position:absolute;top:2925px;left:0;width:1200px;height:289px;background:var(--navy);color:#d8defa;font-size:14px;line-height:31px}
.footer-col{position:absolute;top:34px}
.footer-col h4{font-family:"Jost",sans-serif;font-weight:500;font-size:20px;color:var(--white);margin-bottom:12px}
.col-about{left:79px;width:250px}
.read-more{color:var(--white);font-weight:700}
.col-map{left:343px}
.col-map ul{list-style:none}
.col-map li{display:flex;align-items:center;gap:14px}
.col-map li::before{content:"";width:9px;height:9px;border-radius:50%;background:var(--white)}
.col-contact{left:611px;width:280px}
.contact-line{display:flex;gap:16px;margin-bottom:10px}
.contact-line svg{flex:none;margin-top:7px}
.footer-brand{position:absolute;left:896px;top:40px;width:229px;height:150px;display:flex;align-items:center;justify-content:center;gap:10px;font-family:"Jost",sans-serif;font-weight:600;font-size:34px;color:var(--white)}
.footer-brand .dot{width:22px;height:22px;border-radius:50%;background:var(--white)}
.copyright{position:absolute;left:896px;top:196px;width:229px;text-align:center;font-size:14px;line-height:25px}
</style>
</head>
<body>

<header class="site-header">
  <div class="brand"><span class="brand-dot"></span>Quorbelline</div>
  <nav class="main-nav">
    <span class="active">HOME</span><span>ABOUT US</span><span>PROCESS</span><span>EXECUTIVE TEAM</span><span>CONTACT US</span>
    <span class="btn-download">DOWNLOAD</span>
  </nav>
</header>

<section class="hero">
  <div class="hero-card">
    <h1 class="heading">Digital Assest Management</h1>
    <p>Quorbelline enable companies and investors to facilities business operation in modern digital world, including asset management on hedge fund strategy model.</p>
  </div>
  <div class="hero-scene" role="img" aria-label="Illustration of an office of traders working at computer desks"></div>
</section>

<section class="definition">
  <div class="mark"></div>
  <h2 class="heading">Defination of Quorbelline</h2>
  <p>Quorbelline process and manages on hedge fund strategy models which invests in a diversified portfolio of blockchain tokens. Blockchain tokens are emerging which add a monetary incentive layer to p2p protocols and facilitate equity crowdfunding that anyone in the world can participate in. This means open source software developers can monetize their networks at the protocol level and users of the network are the equity owners of the network. For this conditions, returns will go to holders of the tokens.</p>
  <span class="btn-outline">Know More</span>
</section>

<section class="process">
  <h2 class="heading">Our Process</h2>
  <div class="subtitle">Hedge Fund Model</div>
  <p>Quorbelline run on closed-end fund (CEF) model which offers its shares to investors and utilize the fund to speculate and invest in the innovative blockchain tokens. Quorbelline will charge an upfront annual operation fee 4% of the money raised during the ICO. After that, the fund will charge a quarterly performance of 50% on the net profit made.</p>
  <div class="process-visual" role="img" aria-label="Photo of hands holding a tablet showing a chart of net profit against performance fee"></div>
</section>
<div class="side-wedge left"></div>
<div class="side-wedge right"></div>

<div class="fee-steps">
  <div class="fee-step"><div class="fee-cell">50 % of net profit is distributed to investors</div><div class="fee-cell fee-value">50%</div></div>
  <div class="fee-step"><div class="fee-cell fee-value">0 %</div><div class="fee-cell">0 – 5 % net profit &gt; 0% performance fee</div></div>
  <div class="fee-step"><div class="fee-cell">5 – 10% net profit &gt; 5% performance fee</div><div class="fee-cell fee-value">5 %</div></div>
  <div class="fee-step"><div class="fee-cell fee-value">13 %</div><div class="fee-cell">10-15 % net profit &gt; 13% performance fee</div></div>
  <div class="fee-step"><div class="fee-cell">&gt; 15% net profit &gt; 15% performance fee</div><div class="fee-cell fee-value">15 %</div></div>
</div>
<div class="reinvest">The remainder ( 50% minus performance fee, so at least 35%) is reinvested</div>

<section class="team">
  <h2 class="heading">Executive Team</h2>
  <div class="subtitle">We Are Ready To Help You</div>
  <article class="team-card" style="left:79px">
    <div class="portrait" role="img" aria-label="Portrait photo of Vethran Olsavik"></div>
    <h3>Vethran Olsavik</h3>
    <div class="role">Director</div>
    <p>As a hedge fund manager, Olsavik is the Chief Executive Officer of Harrowmere Capital LLC.</p>
  </article>
  <article class="team-card featured" style="left:443px">
    <div class="portrait" role="img" aria-label="Portrait photo of Daliko Ferrant"></div>
    <h3>Daliko Ferrant</h3>
    <div class="role">Technical advisor</div>
    <p>Ferrant has various experienced on crypto currency and blockchain technology He created what was the world's.</p>
  </article>
  <article class="team-card" style="left:810px">
    <div class="portrait" role="img" aria-label="Portrait photo of Coren Maybridge-Tull"></div>
    <h3>Coren Maybridge-Tull</h3>
    <div class="role">Marketing Consultant</div>
    <p>Maybridge-Tull embeds a decade of experience in brand building, strategic planning, and marketing.</p>
  </article>
</section>

<section class="more-info">
  <div class="slant"></div>
  <div class="big-mark"><span class="dot"></span>Quorbelline</div>
  <h2 class="heading">For More Information</h2>
  <p>Quorbelline process and manages on hedge fund strategy models which invests in a diversified portfolio of blockchain tokens. Blockchain tokens are emerging which add a monetary.</p>
  <span class="btn-solid">Download Whitepaper</span>
</section>

<footer class="site-footer">
  <div class="footer-col col-about">
    <h4>ABOUT US</h4>
    <div>Quorbelline process and manages on hedge fund strategy models which invests in a diversified portfolio of blockchain tokens. Blockchain tokens are emerging which add a monetary incentive layer to p2p....</div>
    <div class="read-more">Read More... &raquo;</div>
  </div>
  <div class="footer-col col-map">
    <h4>SITE MAP</h4>
    <ul><li>Home</li><li>About Us</li><li>Process</li><li>Executive Team</li><li>Contact Us</li><li>Download</li></ul>
  </div>
  <div class="footer-col col-contact">
    <h4>CONTACT US</h4>
    <div class="contact-line">
      <svg width="14" height="20" viewBox="0 0 14 20"><path d="M7 0a7 7 0 0 0-7 7c0 5 7 13 7 13s7-8 7-13a7 7 0 0 0-7-7zm0 10a3 3 0 1 1 0-6 3 3 0 0 1 0 6z" fill="#fff"/></svg>
      <span>Suite 12-04, 9/F, North Wing, Larkspur Trade Centre, 42 Pellow Road, Eastgate District, Marrowfield.</span>
    </div>
    <div class="contact-line">
      <svg width="18" height="18" viewBox="0 0 18 18"><path d="M4 1l3 4-2 2c1 2 4 5 6 6l2-2 4 3-2 3C8 17 1 10 1 3z" fill="#fff"/></svg>
      <span>555 014 2290</span>
    </div>
    <div class="contact-line">
      <svg width="18" height="14" viewBox="0 0 18 14"><rect width="18" height="14" rx="2" fill="#fff"/><path d="M1 2l8 6 8-6" stroke="#1b2a8c" stroke-width="1.6" fill="none"/></svg>
      <span>info@quorbelline.com</span>
    </div>
  </div>
  <div class="footer-brand"><span class="dot"></span>Quorbelline</div>
  <div class="copyright">©Quorbelline -2017 All rights reserved.</div>
</footer>

</body>
</html>
```